Design a New Business Card for Our Company

We are looking for fresh, unique, and a modern business card that reflects our roots as digital marketing agency focused on SEM.

Industry/Entity Type

Marketing

Contact Information for Business Card

looking for very unique out of the box designs. clean and modern that compliments our logo

Requirements
Must have
• colors should match our logo
• Front should have name, address, email, and phone/fax of the person, phone/fax are the same number
• back should have our url

```html
<!DOCTYPE html>
<html lang="en">
<head>
<meta charset="utf-8">
<title>Brightpath Digital – Business Card</title>
<link rel="stylesheet" href="https://fonts.googleapis.com/css2?family=Open+Sans:wght@400;600;700&display=swap">
<style>
  :root {
    --brand-blue: #5896d0;
    --accent-blue: #4a86c8;
    --logo-grey: #a3a3a3;
    --text-grey: #8a8a8a;
    --card-white: #ffffff;
    --stage: #2b2b2d;
  }
  * { margin: 0; padding: 0; box-sizing: border-box; }
  html, body { width: 1200px; height: 925px; overflow: hidden; }
  body {
    background: var(--stage);
    font-family: "Open Sans", Arial, sans-serif;
    display: flex;
    align-items: center;
    justify-content: center;
    gap: 48px;
  }
  .card {
    position: relative;
    width: 525px;
    height: 300px;
    overflow: hidden;
  }

  /* Back side */
  .card--back { background: var(--brand-blue); color: var(--card-white); }
  .card--back .brand {
    position: absolute;
    left: 0; right: 0; top: 100px;
    display: flex; align-items: center; justify-content: center; gap: 14px;
  }
  .brand-dot {
    width: 40px; height: 40px; border-radius: 50%;
    background: currentColor;
  }
  .brand-name {
    font-weight: 700;
    font-size: 40px;
    line-height: 1;
    letter-spacing: -0.5px;
  }
  .card--back .site {
    position: absolute;
    right: 34px; bottom: 30px;
    font-size: 13px;
    letter-spacing: 0.2px;
  }

  /* Front side */
  .card--front { background: var(--card-white); }
  .card--front .brand {
    position: absolute;
    left: 170px; top: 52px;
    display: flex; align-items: center; gap: 12px;
    color: var(--logo-grey);
  }
  .card--front .brand-name { font-size: 36px; }
  .card--front .brand-dot { width: 34px; height: 34px; background: var(--accent-blue); }

  .company-address {
    position: absolute;
    right: 30px; bottom: 34px;
    text-align: right;
    font-size: 12.5px;
    line-height: 1.4;
    color: var(--text-grey);
  }
  .company-address .company { color: var(--accent-blue); }

  .rule {
    position: absolute;
    left: 26px; top: 0; bottom: 0;
    width: 1.5px;
    background: var(--accent-blue);
  }
  .person {
    position: absolute;
    left: 50px; top: 148px;
  }
  .person-name { font-size: 18px; font-weight: 700; color: var(--accent-blue); line-height: 1.2; }
  .person-role { font-size: 13px; color: var(--text-grey); }

  .contacts {
    position: absolute;
    left: 17px; top: 200px;
    list-style: none;
  }
  .contacts li {
    display: flex; align-items: center; gap: 14px;
    height: 20px;
    font-size: 13px;
    color: var(--text-grey);
  }
  .contacts svg { width: 19px; height: 19px; flex: none; }
</style>
</head>
<body>

  <section class="card card--back" aria-label="Card back">
    <div class="brand">
      <span class="brand-dot"></span>
      <span class="brand-name">brightpath</span>
    </div>
    <p class="site">www.brightpathdigital.com</p>
  </section>

  <section class="card card--front" aria-label="Card front">
    <div class="brand">
      <span class="brand-dot"></span>
      <span class="brand-name">brightpath</span>
    </div>

    <address class="company-address">
      <span class="company">Brightpath Digital</span><br>
      48 Harbor Lane, Suite 210,<br>
      Tacoma, WA 98402
    </address>

    <span class="rule"></span>

    <div class="person">
      <p class="person-name">Nora Ellison</p>
      <p class="person-role">Owner</p>
    </div>

    <ul class="contacts">
      <li>
        <svg viewBox="0 0 20 20" aria-hidden="true"><circle cx="10" cy="10" r="9.5" fill="#4a86c8"/><path d="M7 5.5l2 2-1 1.3c.6 1.4 1.6 2.4 3 3l1.3-1 2 2-1.2 1.5c-3.5-.4-6.2-3.1-6.6-6.6z" fill="#fff"/></svg>
        555.214.3080
      </li>
      <li>
        <svg viewBox="0 0 20 20" aria-hidden="true"><circle cx="10" cy="10" r="9.5" fill="#4a86c8"/><rect x="6" y="8" width="8" height="6" fill="#fff"/><rect x="7.5" y="5" width="5" height="3" fill="none" stroke="#fff"/></svg>
        555.214.3080
      </li>
      <li>
        <svg viewBox="0 0 20 20" aria-hidden="true"><circle cx="10" cy="10" r="9.5" fill="#4a86c8"/><rect x="5" y="6.5" width="10" height="7" fill="#fff"/><path d="M5 6.5l5 4 5-4" fill="none" stroke="#4a86c8"/></svg>
        info@brightpathdigital.com
      </li>
      <li>
        <svg viewBox="0 0 20 20" aria-hidden="true"><circle cx="10" cy="10" r="9.5" fill="#4a86c8"/><circle cx="10" cy="10" r="5" fill="none" stroke="#fff"/><path d="M5 10h10M10 5c-2.5 3-2.5 7 0 10M10 5c2.5 3 2.5 7 0 10" fill="none" stroke="#fff" stroke-width=".8"/></svg>
        www.brightpathdigital.com
      </li>
    </ul>
  </section>

</body>
</html>
```